Concierge Healthcare Business Card Design and Logo

We need a logo and business card design for a new company called "Sound Haven". We will provide concierge audiological care, hearing aids, hearing exams, custom hearing protection etc to patients in the comfort of their homes and offices. We would like a sleek and modern design preferably with an Ear related logo.

Target Market(s)

People with hearing loss, Hunters, Musicians
My usual clientele are older individuals so usually 50+ years old

Industry/Entity Type

Health Care

Contact Information for Business Card

Celia Brandt, AuD
Audiologist
512-648-2917
soundhaven@mailvoro.com
www.soundhaven-vorel.com

Logo Text

Sound Haven

Number of Pages Required

3 page

```html
<!DOCTYPE html>
<html lang="en">
<head>
<meta charset="utf-8">
<title>Sound Haven — Business Card</title>
<link rel="stylesheet" href="https://fonts.googleapis.com/css2?family=Open+Sans:wght@400;600;700&display=swap">
<style>
  :root {
    --backdrop: #e9e7e4;
    --card-white: #ffffff;
    --brand-blue: #0b8fb8;
    --brand-green: #1fb50f;
    --wordmark-green: #1aa80f;
    --text-light: #ffffff;
    --rule-light: rgba(255, 255, 255, 0.28);
  }
  * { box-sizing: border-box; margin: 0; padding: 0; }
  html, body {
    width: 1200px;
    height: 900px;
    overflow: hidden;
    background: var(--backdrop);
    font-family: "Open Sans", Arial, sans-serif;
  }
  .canvas {
    position: relative;
    width: 1200px;
    height: 900px;
  }
  .card {
    position: absolute;
    background: var(--card-white);
    overflow: hidden;
    box-shadow: 0 6px 18px rgba(0, 0, 0, 0.12);
  }

  /* Front card */
  .card--front {
    left: 78px;
    top: 34px;
    width: 588px;
    height: 364px;
  }
  .card--front .brand-area {
    height: 156px;
    display: flex;
    align-items: center;
    padding-left: 34px;
    padding-top: 16px;
  }
  .wordmark {
    font-weight: 400;
    font-size: 56px;
    letter-spacing: -0.5px;
    line-height: 1;
    white-space: nowrap;
  }
  .card--front .wordmark { color: var(--wordmark-green); }
  .details-band {
    position: absolute;
    left: 0;
    top: 156px;
    width: 100%;
    height: 208px;
    background: var(--brand-blue);
    color: var(--text-light);
  }
  .holder-name {
    position: absolute;
    left: 30px;
    top: 17px;
    font-weight: 600;
    font-size: 19px;
    line-height: 1.3;
  }
  .holder-role {
    position: absolute;
    left: 30px;
    top: 43px;
    font-size: 15px;
    line-height: 1.3;
  }
  .contact-list {
    position: absolute;
    left: 0;
    top: 99px;
    width: 247px;
    list-style: none;
  }
  .contact-item {
    display: flex;
    align-items: center;
    height: 31px;
    padding-left: 33px;
    font-size: 15px;
    line-height: 1;
    white-space: nowrap;
    border-top: 1px solid var(--rule-light);
  }
  .contact-item:first-child { border-top: none; }
  .contact-icon {
    width: 12px;
    height: 12px;
    margin-right: 12px;
    flex: none;
  }

  /* Back card */
  .card--back {
    left: 388px;
    top: 505px;
    width: 567px;
    height: 352px;
  }
  .brand-band {
    position: absolute;
    left: 0;
    top: 110px;
    width: 100%;
    height: 131px;
    background: var(--brand-green);
    display: flex;
    align-items: center;
    justify-content: center;
  }
  .card--back .wordmark { color: var(--text-light); }
</style>
</head>
<body>
<main class="canvas">

  <section class="card card--front" aria-label="Business card front">
    <div class="brand-area">
      <span class="wordmark">Sound Haven</span>
    </div>
    <div class="details-band">
      <p class="holder-name">Celia Brandt</p>
      <p class="holder-role">Audiologist</p>
      <ul class="contact-list">
        <li class="contact-item">
          <svg class="contact-icon" viewBox="0 0 24 24" aria-hidden="true">
            <path fill="#fff" d="M6.6 10.8a15.2 15.2 0 0 0 6.6 6.6l2.2-2.2a1 1 0 0 1 1-.25 11.4 11.4 0 0 0 3.6.57 1 1 0 0 1 1 1V20a1 1 0 0 1-1 1A17 17 0 0 1 3 4a1 1 0 0 1 1-1h3.5a1 1 0 0 1 1 1c0 1.25.2 2.45.57 3.57a1 1 0 0 1-.25 1z"/>
          </svg>
          512-648-2917
        </li>
        <li class="contact-item">
          <svg class="contact-icon" viewBox="0 0 24 24" aria-hidden="true">
            <path fill="#fff" d="M2 5h20v14H2z"/>
            <path fill="none" stroke="#0b8fb8" stroke-width="2" d="M2 5l10 8 10-8"/>
          </svg>
          soundhaven@mailvoro.com
        </li>
        <li class="contact-item">
          <svg class="contact-icon" viewBox="0 0 24 24" aria-hidden="true">
            <g fill="none" stroke="#fff" stroke-width="2.6" stroke-linecap="round">
              <path d="M10 14a4 4 0 0 0 5.7 0l3.6-3.6a4 4 0 0 0-5.7-5.7l-1.2 1.2"/>
              <path d="M14 10a4 4 0 0 0-5.7 0l-3.6 3.6a4 4 0 0 0 5.7 5.7l1.2-1.2"/>
            </g>
          </svg>
          www.soundhaven-vorel.com
        </li>
      </ul>
    </div>
  </section>

  <section class="card card--back" aria-label="Business card back">
    <div class="brand-band">
      <span class="wordmark">Sound Haven</span>
    </div>
  </section>

</main>
</body>
</html>
```